Dalvick's Business Card

I need some designs for a new business card including the new logo attached. An old example of our business card is also attached to show all the data that should be included on the new design.
**I added some more examples someone had mocked up**

Contact Information for Business Card

Should include all info on other examples uploaded.

```html
<!DOCTYPE html>
<html lang="en">
<head>
<meta charset="utf-8">
<title>Dalvick's Business Card</title>
<link href="https://fonts.googleapis.com/css2?family=Montserrat:wght@500;700;800&family=Questrial&display=swap" rel="stylesheet">
<style>
  :root {
    --brand-blue: #0f6fb8;
    --brand-red: #e8202a;
    --card-white: #ffffff;
    --backdrop: #e5e4e6;
  }
  * { margin: 0; padding: 0; box-sizing: border-box; }
  html, body { width: 1200px; height: 1200px; overflow: hidden; background: var(--backdrop); }
  body { position: relative; font-family: "Questrial", sans-serif; }

  .card {
    position: absolute;
    left: 110px;
    width: 980px;
    height: 560px;
    background: var(--card-white);
    box-shadow: 0 6px 18px rgba(0,0,0,0.12);
    overflow: hidden;
  }
  .card-front { top: 30px; }
  .card-back { top: 610px; }

  .band {
    position: absolute;
    left: 0; right: 0;
    height: 72px;
    display: flex; align-items: center; justify-content: center;
    color: var(--card-white);
    font-family: "Montserrat", sans-serif;
    font-weight: 500;
    letter-spacing: 1.5px;
    font-size: 27px;
  }
  .band-top { top: 0; background: var(--brand-blue); }
  .band-bottom { bottom: 0; background: var(--brand-red); font-size: 22px; }
  .notch { position: absolute; width: 60px; height: 22px; }
  .notch-top { top: 72px; left: 430px; }
  .notch-bottom { bottom: 72px; left: 500px; }

  .brand {
    position: absolute;
    display: flex; align-items: center;
  }
  .brand-mark {
    border-radius: 50%;
    background: var(--brand-blue);
    flex: none;
  }
  .brand-text { display: flex; flex-direction: column; }
  .brand-name {
    font-family: "Montserrat", sans-serif;
    font-weight: 800;
    color: var(--brand-blue);
    line-height: 1;
    letter-spacing: 2px;
  }
  .brand-tagline {
    font-family: "Montserrat", sans-serif;
    font-weight: 700;
    color: var(--brand-red);
    letter-spacing: 1px;
  }

  .card-front .brand { left: 0; right: 0; top: 205px; justify-content: center; gap: 26px; }
  .card-front .brand-mark { width: 110px; height: 110px; }
  .card-front .brand-name { font-size: 104px; }
  .card-front .brand-tagline { font-size: 22px; margin-top: 6px; }

  .card-back .brand { left: 0; right: 0; top: 70px; justify-content: center; gap: 16px; }
  .card-back .brand-mark { width: 62px; height: 62px; }
  .card-back .brand-name { font-size: 56px; }
  .card-back .brand-tagline { font-size: 12px; margin-top: 4px; }

  .credentials {
    position: absolute; left: 0; right: 0; top: 185px;
    text-align: center;
    color: var(--brand-blue);
    font-size: 30px;
    letter-spacing: 2px;
    line-height: 1.35;
  }
  .owner-name {
    position: absolute; left: 0; right: 0; top: 298px;
    text-align: center;
    font-family: "Montserrat", sans-serif;
    font-weight: 800;
    color: var(--brand-red);
    font-size: 46px;
    letter-spacing: 1px;
  }
  .contact-icons {
    position: absolute; left: 0; right: 0; top: 376px;
    display: flex; justify-content: center; gap: 12px;
  }
  .contact-icons svg { width: 38px; height: 38px; }
  .contact-lines {
    position: absolute; left: 0; right: 0; top: 424px;
    text-align: center;
    color: var(--brand-blue);
    font-size: 30px;
    letter-spacing: 1px;
    line-height: 1.3;
  }
</style>
</head>
<body>

  <section class="card card-front">
    <div class="band band-top">SERVES FAIRBROOK, IA &amp; SURROUNDING AREAS</div>
    <svg class="notch notch-top" viewBox="0 0 60 22" aria-hidden="true"><polygon points="0,0 60,0 30,22" fill="var(--brand-blue)"/></svg>

    <div class="brand">
      <span class="brand-mark"></span>
      <div class="brand-text">
        <span class="brand-name">DALVICK'S</span>
        <span class="brand-tagline">AIR CONDITIONING &amp; HEATING SERVICE</span>
      </div>
    </div>

    <svg class="notch notch-bottom" viewBox="0 0 60 22" aria-hidden="true"><polygon points="0,22 60,22 30,0" fill="var(--brand-red)"/></svg>
    <div class="band band-bottom">CALL TODAY FOR ALL YOUR HVAC, REFRIGERATION &amp; PLUMBING NEEDS</div>
  </section>

  <section class="card card-back">
    <div class="brand">
      <span class="brand-mark"></span>
      <div class="brand-text">
        <span class="brand-name">DALVICK'S</span>
        <span class="brand-tagline">AIR CONDITIONING &amp; HEATING SERVICE</span>
      </div>
    </div>

    <p class="credentials">LICENSED &amp; INSURED<br>FAMILY OWNED &amp; OPERATED</p>
    <p class="owner-name">STEVE DALVICK</p>

    <div class="contact-icons">
      <svg viewBox="0 0 40 40" role="img" aria-label="Phone">
        <circle cx="20" cy="20" r="19" fill="var(--brand-blue)"/>
        <path d="M13 11c1-1 2.5-1 3 0l2 4c.4.8 0 1.6-.6 2l-1.4 1c1 2.4 2.8 4.3 5 5.3l1-1.4c.5-.6 1.3-.9 2-.5l4 2c1 .5 1 2 0 3l-1.5 1.5c-1.5 1.5-5 1-9-3s-4.8-7.5-3.3-9z" fill="#fff"/>
      </svg>
      <svg viewBox="0 0 40 40" role="img" aria-label="Email">
        <circle cx="20" cy="20" r="19" fill="var(--brand-blue)"/>
        <rect x="10" y="13" width="20" height="14" rx="2" fill="#fff"/>
        <polyline points="10.5,14 20,21.5 29.5,14" fill="none" stroke="var(--brand-blue)" stroke-width="2"/>
      </svg>
    </div>

    <p class="contact-lines">555.014.2290<br>hvacdalvick@mailbox.com</p>
  </section>

</body>
</html>
```